We want to design total new business card and logo for Kestrel Building Services Ltd

Our company name Kestrel Building Services Ltd. Design new logo and business card , need hi-end luxury style art for architecture and construction industry. The card should simple but stylish. Our business focus on CONNECT tradesman to construction company, help marketing construction company tender oversea projects, managing franchise in construction sector, delivery amazing services to our client, so Logo should show the CONNECTION IDEA, CONNECTING PEOPLE, LUXURY. Visit our website for more information: kestrelgroup.example.nz

Target Market(s)

Directors or managers

Industry/Entity Type

Construction Company

Contact Information for Business Card

Name, Title, Mobile, Email, Website

Font styles to use
Serif

Colors

Designer to choose colors to be used in the design.

Requirements
Must have
• Simple and luxury, connection icon
Nice to have
• Special materials, plastic card, look through,...
• Look new ideas.

```html
<!DOCTYPE html>
<html lang="en">
<head>
<meta charset="utf-8">
<title>Kestrel Building Services – Business Card</title>
<link rel="stylesheet" href="https://fonts.googleapis.com/css2?family=Open+Sans:wght@400;600&family=Playfair+Display:wght@700&display=swap">
<style>
  :root {
    --backdrop: #3a3a3c;
    --brand-blue: #06a8c8;
    --card-white: #ffffff;
    --ink: #2b2b2b;
    --rule: #d6d6d6;
    --heading-font: "Playfair Display", Georgia, serif;
    --text-font: "Open Sans", Arial, sans-serif;
  }
  html, body {
    margin: 0;
    width: 1200px;
    height: 1200px;
    overflow: hidden;
    background: var(--backdrop);
    font-family: var(--text-font);
  }
  .canvas {
    position: relative;
    width: 1200px;
    height: 1200px;
  }
  .card {
    position: absolute;
    left: 250px;
    width: 700px;
    height: 400px;
    box-sizing: border-box;
    box-shadow: 0 10px 30px rgba(0,0,0,.35);
  }
  .brand-dot {
    position: absolute;
    width: 50px;
    height: 50px;
    border-radius: 50%;
  }

  /* Front */
  .card-front {
    top: 150px;
    background: var(--brand-blue);
    color: var(--card-white);
    border-radius: 110px 0 110px 0;
    text-align: center;
  }
  .card-front .brand-dot {
    top: 90px;
    left: 325px;
    background: var(--card-white);
  }
  .front-name {
    position: absolute;
    top: 150px;
    left: 0;
    right: 0;
    font-family: var(--heading-font);
    font-weight: 700;
    font-size: 34px;
    letter-spacing: .5px;
    text-transform: uppercase;
  }
  .front-tagline {
    position: absolute;
    top: 212px;
    left: 0;
    right: 0;
    font-size: 16px;
    letter-spacing: 1.5px;
    text-transform: uppercase;
  }
  .front-rules {
    position: absolute;
    top: 262px;
    left: 140px;
    right: 140px;
    display: flex;
    align-items: center;
    gap: 14px;
  }
  .front-rules .rule {
    flex: 1;
    height: 1px;
    background: rgba(255,255,255,.8);
  }
  .front-rules .dot {
    width: 10px;
    height: 10px;
    border-radius: 50%;
    background: var(--card-white);
  }

  /* Back */
  .card-back {
    top: 620px;
    background: var(--card-white);
    color: var(--ink);
    border-radius: 0 110px 0 110px;
  }
  .card-back .brand-dot {
    top: 38px;
    right: 190px;
    background: var(--brand-blue);
  }
  .back-name {
    position: absolute;
    top: 98px;
    right: 50px;
    color: var(--brand-blue);
    font-family: var(--heading-font);
    font-weight: 700;
    font-size: 30px;
    text-transform: uppercase;
  }
  .divider {
    position: absolute;
    top: 212px;
    left: 40px;
    right: 60px;
    height: 2px;
    background: var(--rule);
  }
  .person {
    position: absolute;
    top: 152px;
    left: 40px;
  }
  .person-name {
    color: var(--brand-blue);
    font-family: var(--heading-font);
    font-weight: 700;
    font-size: 24px;
    letter-spacing: .5px;
    text-transform: uppercase;
    line-height: 1.2;
  }
  .person-title {
    font-size: 18px;
    line-height: 1.2;
  }
  .contacts {
    position: absolute;
    top: 228px;
    left: 40px;
    margin: 0;
    padding: 0;
    list-style: none;
    font-size: 18px;
    line-height: 27px;
  }
  .contacts li {
    display: flex;
    align-items: center;
    gap: 10px;
  }
  .contacts svg {
    width: 15px;
    height: 15px;
    fill: var(--brand-blue);
  }
  .address {
    position: absolute;
    top: 240px;
    right: 60px;
    text-align: right;
    font-size: 19px;
    line-height: 27px;
  }
  .address-company {
    color: var(--brand-blue);
    text-transform: uppercase;
  }
</style>
</head>
<body>
<main class="canvas">
  <section class="card card-front">
    <span class="brand-dot" aria-hidden="true"></span>
    <div class="front-name">Kestrel Building Services</div>
    <div class="front-tagline">Amazing services affordable price</div>
    <div class="front-rules"><span class="rule"></span><span class="dot"></span><span class="rule"></span></div>
  </section>

  <section class="card card-back">
    <span class="brand-dot" aria-hidden="true"></span>
    <div class="back-name">Kestrel Building Services</div>
    <div class="divider"></div>
    <div class="person">
      <div class="person-name">Marcus Reid</div>
      <div class="person-title">Managing Director</div>
    </div>
    <ul class="contacts">
      <li><svg viewBox="0 0 16 16" aria-hidden="true"><path d="M3 1h3l1 4-2 1a9 9 0 0 0 5 5l1-2 4 1v3a2 2 0 0 1-2 2A13 13 0 0 1 1 3a2 2 0 0 1 2-2z"/></svg>0800 555 014</li>
      <li><svg viewBox="0 0 16 16" aria-hidden="true"><path d="M3 1h3l1 4-2 1a9 9 0 0 0 5 5l1-2 4 1v3a2 2 0 0 1-2 2A13 13 0 0 1 1 3a2 2 0 0 1 2-2z"/></svg>021 555 0192</li>
      <li><svg viewBox="0 0 16 16" aria-hidden="true"><path d="M1 3h14v10H1z M1 3l7 6 7-6" stroke="#fff" stroke-width="1"/></svg>info@kestrelgroup.example.nz</li>
      <li><svg viewBox="0 0 16 16" aria-hidden="true"><circle cx="8" cy="8" r="7"/></svg>www.kestrelgroup.example.nz</li>
    </ul>
    <div class="address">
      <div class="address-company">Kestrel Building Services Ltd</div>
      <div>12 Harbour Lane, Riverton</div>
      <div>Auckland 2099, New Zealand</div>
    </div>
  </section>
</main>
</body>
</html>
```